Web Design

We need a website for a company based in Doha Qatar called
Lumara Maid Service.

It is the number one maid cleaning service company, and we have branches all over qatar.

Luxury Cleaning Service Provider.

The color scheme is gold, yellow and black like the logo.

Before they get to the website, there is an intro video.

The website should depict luxury.

Target Market(s)

People who need maids at their houses.

Industry/Entity Type

Cleaning Service

Requirements
Must have
• Luxury, Sleek, Modern

The opening sequence is a video which I already have. Its too big to upload here so I am going to put it on youtube.

After the opening sequence, the home page should have a widescreen photo background and it should change every five seconds, the first background photo should be of qatar westbay skyline. Then the second background should be of maid photos in cleaning positions. Then the third background should be of cleaner photos etc.

We will send you all the tabs and all the content later.

```html
<!DOCTYPE html>
<html lang="en">
<head>
<meta charset="utf-8">
<title>Lumara Maid Service</title>
<link href="https://fonts.googleapis.com/css2?family=Montserrat:wght@400;500;600;700&family=Lato:wght@400;700&display=swap" rel="stylesheet">
<style>
  :root{
    --gold-light:#f7d65c;
    --gold:#e9b52a;
    --gold-deep:#b88207;
    --gold-text:#d99a0d;
    --brown-dark:#2a1406;
    --brown-logo:#3a1d08;
    --ink:#2b2b2b;
    --white:#ffffff;
    --black:#111111;
  }
  *{margin:0;padding:0;box-sizing:border-box}
  html,body{width:867px;height:1200px;overflow:hidden}
  body{position:relative;background:var(--white);font-family:"Lato",sans-serif;color:var(--ink)}

  .hero-backdrop{position:absolute;left:0;top:0;width:867px;height:476px;
    background:linear-gradient(180deg,#8c8c8c 0%,#a9a9a9 35%,#6f6f6f 70%,#3e3e3e 100%)}
  .top-strip{position:absolute;left:0;top:0;width:867px;height:4px;background:var(--brown-dark)}

  .nav-bar{position:absolute;left:86px;top:4px;width:695px;height:79px;
    background:linear-gradient(180deg,#f3cc4e 0%,var(--gold-light) 45%,var(--gold) 100%);
    box-shadow:0 2px 4px rgba(0,0,0,.25)}
  .nav{position:absolute;top:38px;display:flex;gap:21px;font-family:"Montserrat",sans-serif;font-size:9.5px;font-weight:600;color:#3a2408;white-space:nowrap}
  .nav-left{left:31px}
  .nav-right{left:434px}

  .logo-box{position:absolute;left:358px;top:0;width:152px;height:122px;
    background:linear-gradient(180deg,#4a2a0e 0%,var(--brown-logo) 40%,#1a0c03 100%);
    display:flex;align-items:center;justify-content:center;gap:7px}
  .logo-dot{width:10px;height:10px;border-radius:50%;background:var(--gold)}
  .logo-name{font-family:"Montserrat",sans-serif;font-size:11px;font-weight:600;color:var(--gold);line-height:1.3;text-transform:uppercase;letter-spacing:.5px}

  .hero-slide{position:absolute;left:86px;top:97px;width:695px;height:337px;
    background:linear-gradient(100deg,#d8cdbf 0%,#cbbca8 40%,#b79a7b 65%,#5d6f80 100%)}
  .slider-dots{position:absolute;left:401px;top:407px;display:flex;gap:4px}
  .slider-dots span{width:12px;height:12px;border-radius:50%;border:1.5px solid var(--white)}
  .slider-dots span.active{background:var(--black);border-color:var(--white)}

  .about{position:absolute;left:86px;top:510px;width:695px}
  .about h1{font-family:"Montserrat",sans-serif;font-size:13px;font-weight:700;color:var(--gold-text);margin-bottom:20px}
  .about p{font-size:9.8px;line-height:17.5px;margin-bottom:17px;color:var(--ink)}

  .feature{position:absolute;top:741px;width:208px;height:344px}
  .feature-1{left:86px}.feature-2{left:329px}.feature-3{left:570px}
  .feature-photo{height:145px}
  .feature-1 .feature-photo{background:linear-gradient(90deg,#8a6a44,#c9b49a 60%,#e8e2da)}
  .feature-2 .feature-photo{background:linear-gradient(135deg,#b48a5a,#f1f1f3 45%,#dcdde2)}
  .feature-3 .feature-photo{background:linear-gradient(135deg,#e6e6e6,#f7f7f7 40%,#35a9c7 60%,#eaeaea)}
  .feature-title{height:44px;padding:17px 0 0 16px;font-family:"Montserrat",sans-serif;font-size:9.6px;font-weight:700;color:var(--white);
    background:linear-gradient(180deg,var(--gold-light) 0%,var(--gold) 40%,var(--gold-deep) 100%)}
  .feature-2 .feature-title{padding-left:21px}
  .feature-3 .feature-title{padding-left:23px}
  .feature p{margin-top:13px;font-size:9.8px;line-height:17.4px}
  .btn{position:absolute;left:0;top:321px;height:23px;padding:0 12px;line-height:23px;
    background:var(--black);color:var(--white);font-family:"Montserrat",sans-serif;font-size:10px;font-weight:600}

  .footer{position:absolute;left:0;top:1119px;width:867px;height:81px;background:var(--brown-dark);color:var(--white)}
  .footer-nav{position:absolute;left:94px;top:24px;display:flex;font-family:"Montserrat",sans-serif;font-size:10px;font-weight:500}
  .footer-nav span{padding:0 12px}
  .footer-nav span:first-child{padding-left:0}
  .footer-nav .sep{padding:0}
  .copyright{position:absolute;left:94px;top:49px;font-family:"Montserrat",sans-serif;font-size:9.6px;font-weight:500}
  .social{position:absolute;left:757px;top:30px;width:20px;height:20px;border-radius:50%;border:1.5px solid #d8d8d8}
</style>
</head>
<body>
  <div class="hero-backdrop" role="img" aria-label="Black and white city skyline over the water"></div>
  <div class="top-strip"></div>

  <div class="nav-bar">
    <nav class="nav nav-left"><span>HOME</span><span>ABOUT US</span><span>SERVICES</span><span>TEAM</span></nav>
    <nav class="nav nav-right"><span>LOCATIONS</span><span>TESTIMONIALS</span><span>CONTACT US</span></nav>
  </div>

  <div class="logo-box">
    <span class="logo-dot"></span>
    <span class="logo-name">Lumara<br>Maid Service</span>
  </div>

  <div class="hero-slide" role="img" aria-label="Smiling maid holding rolled white towels in a bright hotel room with sea view"></div>
  <div class="slider-dots"><span class="active"></span><span></span><span></span><span></span></div>

  <section class="about">
    <h1>ABOUT US</h1>
    <p>We aim to be a well-recognized brand in the service industry in Qatar and redefine the quality and standards of service by surpassing expectations of all stakeholders and establish a major presence in the region.</p>
    <p>LUMARA MAID SERVICE was founded on the premise of providing clients with a unique cleaning service that will leave you with a "vacation feeling" in your own home or office. We provide the highest quality professional cleaning services offered in and around Qatar. We specialize in cleaning services for houses, apartments, condominiums, offices, Malls and also commercial janitor services.</p>
    <p>Under British management, we are locally owned and operated, thus you can depend on our responsiveness, accountability and personal attention. When we clean your place, you get the perfect combination of professional quality and personal attention.</p>
  </section>

  <article class="feature feature-1">
    <div class="feature-photo" role="img" aria-label="Smiling maid in apron carrying a tray"></div>
    <div class="feature-title">Service at your Door Step</div>
    <p>LMS boasts about prompt and professional service ready at your door step. You need not worry pick up or drop; LMS will take all those hassles for you. We drop maids at your door step at the said time and we arrange for pick up when the work is done.</p>
    <span class="btn">Read More</span>
  </article>

  <article class="feature feature-2">
    <div class="feature-photo" role="img" aria-label="Hands filling in a quality assurance checklist with a pen"></div>
    <div class="feature-title">Quality Assurance</div>
    <p>Worry-free service with a hundred percent 100% satisfaction guaranteed. In case you are unsatisfied with our service for any reason, our supervisor will visit your location and give you a free service if deemed necessary. In case of any other problem</p>
    <span class="btn">Read More</span>
  </article>

  <article class="feature feature-3">
    <div class="feature-photo" role="img" aria-label="Keyboard with a blue security key"></div>
    <div class="feature-title">Client's Property Security</div>
    <p>All of our cleaners are insured and bonded; therefore you don't need to worry about the safety and security of your place. LMS ensures that client's property is safe and secured. We have strict security system in place. Each day check- in</p>
    <span class="btn">Read More</span>
  </article>

  <footer class="footer">
    <nav class="footer-nav">
      <span>Home</span><span class="sep">|</span><span>About Us</span><span class="sep">|</span><span>Services</span><span class="sep">|</span><span>Jobs</span><span class="sep">|</span><span>Maids</span><span class="sep">|</span><span>FAQ's</span><span class="sep">|</span><span>Testimonials</span><span class="sep">|</span><span>Contact Us</span>
    </nav>
    <div class="copyright">© 2014 Company Name ,All&nbsp; Rights Reserved</div>
    <div class="social"></div>
  </footer>
</body>
</html>
```